"Rafael Lunaro" Business Card

Friends

My name is "Rafael Lunaro" and I need your help! I need a new business card for my personal use.

As background, "Rafael Lunaro" is actually an alias that I use when I meet women. Please use your creative skills to create an amazing business card for me to use!

In addition to including my name and contact details (see the "Must Have" section), you may wish to add a catchphrase or a title if you think it would help me :)

For background, please see:

http://www.dailyquillpost.example/2013/07/23/gerald-fenwick-rafael-lunaro_n_3640295.html

Looking forward to seeing what you can do for me.

Hugs and kisses,

Rafael Lunaro [courtesy of PixelGuild]

Target Market(s)

Adult women in New York City...or anywhere really.

Industry/Entity Type

Business

Requirements
Must have
• Please include the following details:

Rafael Lunaro
P: +1-555-4LUNARO
E: secrets@rafaellunaro.example
Nice to have
• You might include a catchphrase, like "Lunaro is my surname But you can call me Mr Velvetpine".

Or perhaps a title, like "Rafael Lunaro, Head of Sexy Times".

You're creative...I will leave the details to you my friends.
Should not have
• Any references to my actual name...because then, what's the point in using an alias?

```html
<!DOCTYPE html>
<html lang="en">
<head>
<meta charset="utf-8">
<title>Rafael Lunaro – Business Card</title>
<link rel="stylesheet" href="https://fonts.googleapis.com/css2?family=Quicksand:wght@500;700&display=swap">
<style>
  :root {
    --backdrop: #b9b9b7;
    --card-light: #6a6a6a;
    --card-dark: #3a3a3a;
    --ink-white: #ffffff;
    --ink-pink: #b03a7e;
    --ink-blue: #5aa6ee;
  }
  html, body {
    margin: 0;
    width: 1200px;
    height: 675px;
    overflow: hidden;
    background: var(--backdrop);
  }
  .stage {
    width: 1200px;
    height: 675px;
    display: flex;
    align-items: center;
    justify-content: center;
  }
  .card {
    width: 840px;
    height: 480px;
    border-radius: 6px;
    background: radial-gradient(ellipse at 45% 35%, var(--card-light) 0%, #4e4e4e 55%, var(--card-dark) 100%);
    box-shadow: 0 6px 18px rgba(0,0,0,0.35);
    font-family: "Quicksand", sans-serif;
    display: flex;
    flex-direction: column;
    align-items: center;
    justify-content: center;
    box-sizing: border-box;
    padding-bottom: 10px;
  }
  .card__name {
    margin: 0;
    font-size: 66px;
    font-weight: 700;
    letter-spacing: 0.5px;
    line-height: 1.1;
    color: var(--ink-white);
  }
  .card__surname { color: var(--ink-pink); }
  .card__title {
    margin: 10px 0 44px;
    font-size: 46px;
    font-weight: 500;
    letter-spacing: 2px;
    color: var(--ink-blue);
  }
  .contact {
    list-style: none;
    margin: 0;
    padding: 0;
    color: var(--ink-white);
    font-size: 38px;
    font-weight: 500;
    line-height: 1.35;
  }
  .contact__item {
    display: flex;
    align-items: center;
    gap: 10px;
  }
  .contact__phone { padding-left: 40px; }
  .contact__icon { width: 26px; height: 26px; fill: var(--ink-white); flex: none; }
</style>
</head>
<body>
  <main class="stage">
    <section class="card">
      <h1 class="card__name">Rafael <span class="card__surname">Lunaro</span></h1>
      <p class="card__title">head of sexy times</p>
      <ul class="contact">
        <li class="contact__item contact__phone">
          <svg class="contact__icon" viewBox="0 0 24 24" aria-hidden="true">
            <path d="M6.6 10.8c1.4 2.8 3.8 5.1 6.6 6.6l2.2-2.2c.3-.3.7-.4 1-.2 1.1.4 2.3.6 3.6.6.6 0 1 .4 1 1V20c0 .6-.4 1-1 1C10.6 21 3 13.4 3 4c0-.6.4-1 1-1h3.5c.6 0 1 .4 1 1 0 1.3.2 2.5.6 3.6.1.3 0 .7-.2 1l-2.3 2.2z"/>
          </svg>
          <span>+1-555-4LUNARO</span>
        </li>
        <li class="contact__item">
          <svg class="contact__icon" viewBox="0 0 24 24" aria-hidden="true">
            <path d="M2 6h20v12H2z M2 6l10 7 10-7" fill="var(--ink-white)" stroke="#4e4e4e" stroke-width="1.2"/>
          </svg>
          <span>secrets@rafaellunaro.example</span>
        </li>
      </ul>
    </section>
  </main>
</body>
</html>
```